Pinecrest Schools Vinyl Banner

Based on the attached images design a image that we will be printed onto a vinyl Banner and used at conventions.

Design liberties are welcome but it needs to look good and the the final submission will need to be submitted in .psd format with all layers being able to be edited.

Make it look good and atract new business

```html
<!DOCTYPE html>
<html lang="en">
<head>
<meta charset="utf-8">
<title>Pinecrest Schools Vinyl Banner</title>
<link href="https://fonts.googleapis.com/css2?family=Oswald:wght@400;500&family=Roboto+Condensed:wght@400;500&family=Cabin:wght@500&family=Montserrat:wght@700&display=swap" rel="stylesheet">
<style>
  :root {
    --page: #e9ebee;
    --banner-blue: #1f5f96;
    --swoosh-blue: #7f9fcb;
    --white: #ffffff;
    --navy: #1b2f57;
    --pill: #1c3a66;
    --link-blue: #1d5790;
  }
  html, body {
    margin: 0;
    width: 1200px;
    height: 1000px;
    overflow: hidden;
    background: var(--page);
  }
  .banner {
    position: absolute;
    left: 24px;
    top: 212px;
    width: 1153px;
    height: 577px;
    background: var(--banner-blue);
    overflow: hidden;
    box-shadow: 0 2px 10px rgba(0,0,0,0.18);
  }
  .banner-shapes {
    position: absolute;
    inset: 0;
  }
  .brand {
    position: absolute;
    left: 0;
    width: 1280px;
    top: 16px;
    text-align: center;
  }
  .brand-name {
    display: inline-flex;
    align-items: center;
    gap: 40px;
    font-family: "Oswald", sans-serif;
    font-weight: 400;
    color: var(--navy);
    font-size: 54px;
    line-height: 54px;
    letter-spacing: 5px;
    text-align: left;
  }
  .brand-mark {
    width: 100px;
    height: 100px;
    background: var(--navy);
  }
  .brand-tagline {
    margin-top: 12px;
    font-family: "Cabin", sans-serif;
    font-weight: 500;
    font-size: 20px;
    color: var(--navy);
  }
  .headline {
    position: absolute;
    left: 0;
    right: 0;
    top: 254px;
    margin: 0;
    text-align: center;
    font-family: "Oswald", sans-serif;
    font-weight: 500;
    font-size: 67px;
    line-height: 80px;
    color: var(--white);
    letter-spacing: 0.5px;
  }
  .headline-rule {
    position: absolute;
    left: 145px;
    width: 862px;
    top: 342px;
    height: 4px;
    background: var(--white);
  }
  .intro {
    position: absolute;
    left: 0;
    right: 0;
    top: 363px;
    margin: 0;
    text-align: center;
    font-family: "Roboto Condensed", sans-serif;
    font-size: 20px;
    color: var(--white);
  }
  .cta {
    position: absolute;
    left: 107px;
    top: 422px;
    margin: 0;
    font-family: "Oswald", sans-serif;
    font-weight: 500;
    font-size: 35px;
    line-height: 48px;
    color: var(--white);
  }
  .phone {
    position: absolute;
    left: 120px;
    top: 480px;
    width: 398px;
    height: 58px;
    border: 2px solid var(--white);
    border-radius: 14px;
    background: var(--pill);
    display: flex;
    align-items: center;
    justify-content: center;
    gap: 12px;
    font-family: "Montserrat", sans-serif;
    font-weight: 700;
    font-size: 43px;
    color: var(--white);
  }
  .phone svg { width: 36px; height: 36px; }
  .website {
    position: absolute;
    right: 32px;
    top: 520px;
    font-family: "Roboto Condensed", sans-serif;
    font-weight: 500;
    font-size: 30px;
    color: var(--link-blue);
  }
</style>
</head>
<body>
  <section class="banner">
    <svg class="banner-shapes" viewBox="0 0 1153 577" width="1153" height="577" aria-hidden="true">
      <path d="M110,0 C260,150 440,214 640,212 C470,205 320,130 200,0 Z" fill="var(--swoosh-blue)"/>
      <path d="M170,0 C310,120 460,212 640,212 C850,210 1040,120 1153,22 L1153,0 Z" fill="var(--white)"/>
      <path d="M520,577 C700,500 900,452 1153,450 L1153,468 C950,470 760,520 600,577 Z" fill="var(--swoosh-blue)"/>
      <path d="M600,577 C760,520 950,472 1153,468 L1153,577 Z" fill="var(--white)"/>
    </svg>

    <div class="brand">
      <div class="brand-name">
        <span class="brand-mark"></span>
        <span>PINECREST<br>SCHOOLS</span>
      </div>
      <div class="brand-tagline">The Complete Online School Payment Solution</div>
    </div>

    <h1 class="headline">ORDER YOUR SCHOOL LUNCH ONLINE</h1>
    <div class="headline-rule"></div>
    <p class="intro">Pinecrest school is an extremely safe, secure and convenient. online ordering system for all your school’s requirement.</p>

    <p class="cta">SIGN UP FOR FREE TRIAL TODAY</p>
    <div class="phone">
      <svg viewBox="0 0 24 24" aria-hidden="true">
        <path d="M6.6 3.5l2.6 2.6-1.6 2.4c1 2.2 2.9 4.1 5.1 5.1l2.4-1.6 2.6 2.6-2 2.9C10.4 17 7 13.6 3.7 6.3z" fill="var(--white)"/>
        <path d="M14 4.5a5.5 5.5 0 0 1 5.5 5.5M14 1.5a8.5 8.5 0 0 1 8.5 8.5" fill="none" stroke="var(--white)" stroke-width="1.6" stroke-linecap="round"/>
      </svg>
      <span>03 9555 0182</span>
    </div>

    <div class="website">www.pinecrestschools.co.au</div>
  </section>
</body>
</html>
```